Marlowe Group needs a business card

I would like the card to be simple but modern and elegant.
I like black and white.
or black and gold.
we are a private finance lender and also are involved in property and property developments.

please look at the business card photos i provided i would like M.G only one one side and all the other details on the other side use fonts that tie in with my theme.

Industry/Entity Type

Finance

Contact Information for Business Card

Marlowe Group (M.G) Daniel Marlowe M: 0413586207 E: danmarl@inboxmail.test

Font styles to use
Other font styles liked:
• Use fonts that would reflect our business

Colors
000000
ffffff

Requirements
Must have
• one side of details
• other side has either M.G or Marlowe Group like in the photos provided

```html
<!DOCTYPE html>
<html lang="en">
<head>
<meta charset="utf-8">
<title>Marlowe Group — Business Card</title>
<link href="https://fonts.googleapis.com/css2?family=Cinzel:wght@400;700&family=Lato:wght@400&display=swap" rel="stylesheet">
<style>
  :root {
    --backdrop: #808080;
    --card: #000000;
    --gold: #f2c41e;
    --white: #ffffff;
    --serif: "Cinzel", "Times New Roman", serif;
    --sans: "Lato", "Helvetica Neue", Arial, sans-serif;
  }
  * { margin: 0; padding: 0; box-sizing: border-box; }
  html, body {
    width: 1200px;
    height: 900px;
    overflow: hidden;
    background: var(--backdrop);
  }
  .stage {
    position: relative;
    width: 1200px;
    height: 900px;
  }
  .card {
    position: absolute;
    top: 309px;
    width: 281px;
    height: 281px;
    background: var(--card);
    border-radius: 22px;
    text-align: center;
  }
  .card--details { left: 306px; }
  .card--brand { left: 613px; }

  .monogram {
    position: absolute;
    left: 0;
    right: 0;
    font-family: var(--serif);
    font-weight: 400;
    color: var(--gold);
    letter-spacing: 2px;
    line-height: 1;
  }
  .card--details .monogram { top: 50px; font-size: 52px; }
  .card--brand .monogram { top: 95px; font-size: 60px; }

  .holder-name {
    position: absolute;
    top: 169px;
    left: 0;
    right: 0;
    font-family: var(--serif);
    font-weight: 700;
    font-size: 15.5px;
    letter-spacing: 0.6px;
    color: var(--gold);
  }
  .divider {
    position: absolute;
    top: 196px;
    left: 79px;
    width: 123px;
    height: 1px;
    background: linear-gradient(90deg, transparent, var(--gold), transparent);
  }
  .contact {
    position: absolute;
    top: 205px;
    left: 0;
    right: 0;
    list-style: none;
    font-family: var(--sans);
    font-size: 13px;
    line-height: 20px;
    color: var(--white);
  }
  .contact__label { color: var(--gold); }

  .company-name {
    position: absolute;
    top: 181px;
    left: 0;
    right: 0;
    font-family: var(--serif);
    font-weight: 400;
    font-size: 16px;
    letter-spacing: 0.5px;
    color: var(--gold);
  }
</style>
</head>
<body>
  <main class="stage">
    <section class="card card--details" aria-label="Contact side">
      <div class="monogram">M.G</div>
      <h1 class="holder-name">DANIEL MARLOWE</h1>
      <div class="divider"></div>
      <ul class="contact">
        <li><span class="contact__label">M:</span> 0413586207</li>
        <li><span class="contact__label">E:</span> danmarl@inboxmail.test</li>
      </ul>
    </section>

    <section class="card card--brand" aria-label="Brand side">
      <div class="monogram">M.G</div>
      <h2 class="company-name">Marlowe Group</h2>
    </section>
  </main>
</body>
</html>
```